Social Media Graphics - Oakline Push REVISED

Create 6-7 individual social media graphics (square size) to encourage folks to join our online course called:

The Harvest Ledger Circle
How to Launch a Multi-Million Business From Scratch
Sign Up Today!

IMPORTANT: Make the largest and most prominent text on the graphic be: How to Launch a Multi-Million Business From Scratch

For the color scheme of the graphics, let's try a blue color palette; make sure the graphics appeal to both men and women

Make sure each graphic contains 1 of the 3 pics attached (crop pic as needed); and make sure one of the graphics is all TEXT only.

Target Market(s)

men and women looking to start a business

Industry/Entity Type

Entrepreneurship

Colors
0054AA
0677BA
7BADD7
CADEEF
E8F1F8

Requirements
Must have
• All the text and use the 3 pics provided; one graphic can be all text; Simple, modern design that's easy to read

```html
<!DOCTYPE html>
<html lang="en">
<head>
<meta charset="utf-8">
<title>The Harvest Ledger Circle – Sign Up</title>
<link href="https://fonts.googleapis.com/css2?family=Archivo+Black&display=swap" rel="stylesheet">
<style>
  :root {
    --blue-deep: #0d4f9e;
    --blue-mid: #1466b8;
    --blue-bright: #0aa6e4;
    --cyan: #16b7ec;
    --navy: #1b2033;
    --white: #ffffff;
    --photo-tone-a: #2a3550;
    --photo-tone-b: #1f4f8a;
  }
  * { margin: 0; padding: 0; box-sizing: border-box; }
  html, body { width: 1200px; height: 1200px; overflow: hidden; }
  body { font-family: "Archivo Black", "Arial Black", sans-serif; color: var(--white); }
  .graphic {
    position: relative;
    width: 1200px; height: 1200px;
    overflow: hidden;
    background: linear-gradient(160deg, var(--blue-deep) 0%, var(--blue-mid) 45%, var(--blue-deep) 100%);
  }
  .graphic__curves { position: absolute; inset: 0; }
  .hosts-photo {
    position: absolute;
    left: 304px; top: 99px; width: 590px; height: 470px;
    background: linear-gradient(90deg, var(--photo-tone-a) 0%, var(--photo-tone-a) 50%, var(--photo-tone-b) 55%, var(--photo-tone-b) 100%);
    border-radius: 6px 6px 0 0;
  }
  .course-pill-glow {
    position: absolute;
    left: 140px; top: 560px; width: 944px; height: 118px;
    background: var(--cyan);
    border-radius: 32px;
  }
  .course-pill {
    position: absolute;
    left: 129px; top: 569px; width: 942px; height: 120px;
    background: var(--navy);
    border-radius: 32px;
    display: flex; align-items: center; justify-content: center;
  }
  .course-name {
    font-size: 44px; line-height: 1; letter-spacing: 1px;
    text-transform: uppercase; white-space: nowrap;
  }
  .headline {
    position: absolute; left: 0; width: 1200px; top: 722px;
    text-align: center; font-size: 62px; line-height: 74px;
    text-transform: uppercase; white-space: nowrap;
  }
  .cta-label {
    position: absolute; left: 127px; width: 978px; top: 1020px;
    display: flex; align-items: center; gap: 22px;
    font-size: 34px; line-height: 1;
  }
  .cta-label::before, .cta-label::after {
    content: ""; flex: 1; height: 2px; background: var(--white);
  }
  .signup-button {
    position: absolute; left: 270px; top: 1067px; width: 660px; height: 66px;
    background: var(--navy);
    display: flex; align-items: center; justify-content: center;
    font-size: 36px; letter-spacing: 3px; text-transform: uppercase;
  }
</style>
</head>
<body>
<main class="graphic">
  <svg class="graphic__curves" width="1200" height="1200" viewBox="0 0 1200 1200" aria-hidden="true">
    <path d="M0 560 C 250 380, 520 330, 760 560 L 760 620 C 520 420, 250 470, 0 640 Z" fill="#0aa6e4" opacity="0.55"/>
    <path d="M0 470 C 300 300, 560 260, 800 520" stroke="#16b7ec" stroke-width="26" fill="none" opacity="0.5"/>
    <path d="M600 0 C 900 150, 1100 400, 1200 700" stroke="#1a8fd6" stroke-width="60" fill="none" opacity="0.5"/>
    <path d="M780 0 C 1000 120, 1150 300, 1200 460" stroke="#2aa8e8" stroke-width="40" fill="none" opacity="0.55"/>
    <path d="M950 0 C 1080 80, 1170 170, 1200 230" stroke="#5cc3f0" stroke-width="30" fill="none" opacity="0.5"/>
    <path d="M0 150 C 200 80, 420 60, 620 120" stroke="#1d72c2" stroke-width="40" fill="none" opacity="0.5"/>
    <path d="M0 900 C 300 760, 800 760, 1200 980" stroke="#1b64b2" stroke-width="50" fill="none" opacity="0.5"/>
  </svg>

  <div class="hosts-photo" role="img" aria-label="Photo of the two course hosts standing side by side, smiling, one in a black turtleneck with arms crossed and one in a denim blazer"></div>

  <div class="course-pill-glow"></div>
  <div class="course-pill">
    <p class="course-name">The Harvest Ledger Circle</p>
  </div>

  <h1 class="headline">How to launch a<br>multi-million<br>business from scratch</h1>

  <div class="cta-label">CTA</div>
  <div class="signup-button">Sign up today</div>
</main>
</body>
</html>
```